KRL Stationery Design Project

Dear Designers,
We need a new stationery design for company to match our new logo.
Designers should provide a design for the following:
1. Business Card: 3.5x2 Inches.
2. Letterhead: A4 size.
3. Envelops: 25x35.5 Cm.
You can keep the Arabic name at the bottom of the logo Or you can use the separate attached Arabic Name.
Please refer to the attached logo guide for design information.
Sample Business Card information:
Name: Tarek Sowan
Position: Operation Manager
Tel: +966 920007164 Ex. 500
Fax: +966 (3)8842617
Mob: +966 (5)00263817
email: tarek@krl-example.com.sa
URL: www.krl-example.com.sa
Address:
Nakheel Heights, Suite 718
Zayed bin Omar Str.
Khobar, 31847
Saudi Arabia
Updates
Dear All,
Please note, we had uploaded our logo along with Arabic writing in Adobe illustrator format (.ai).
Regards,
Karim
Dear All,
A sample data for the business card had been added as per your request.
Regards,
Karim

```html
<!DOCTYPE html>
<html lang="en">
<head>
<meta charset="utf-8">
<title>KRL Business Card</title>
<link rel="stylesheet" href="https://fonts.googleapis.com/css2?family=Source+Sans+3:ital,wght@0,400;0,700;1,700&display=swap">
<style>
  :root {
    --backdrop: #2b2b2d;
    --card: #ffffff;
    --navy: #1a3054;
    --grey: #9a9a9c;
    --ink: #333333;
  }
  * { margin: 0; padding: 0; box-sizing: border-box; }
  html, body { width: 960px; height: 1200px; overflow: hidden; }
  body {
    position: relative;
    background: var(--backdrop);
    font-family: "Source Sans 3", sans-serif;
    color: var(--ink);
  }
  .card {
    position: absolute;
    background: var(--card);
    border-radius: 36px;
    overflow: hidden;
  }
  .card-front { left: 60px; top: 80px; width: 840px; height: 480px; }
  .card-back  { left: 57px; top: 625px; width: 840px; height: 478px; }

  .brand {
    position: absolute;
    display: flex;
    align-items: center;
    color: var(--navy);
    font-weight: 700;
    line-height: 1;
  }
  .brand-mark { background: var(--navy); }
  .card-front .brand { left: 44px; top: 64px; gap: 18px; font-size: 96px; }
  .card-front .brand-mark { width: 40px; height: 40px; }
  .card-back .brand { left: 0; right: 0; top: 170px; justify-content: center; gap: 26px; font-size: 150px; }
  .card-back .brand-mark { width: 60px; height: 60px; }

  .name-band {
    position: absolute;
    left: 540px; top: 232px;
    width: 255px; height: 80px;
    background: var(--navy);
    color: #ffffff;
    padding: 12px 0 0 18px;
  }
  .name-band::after {
    content: "";
    position: absolute;
    left: 255px; top: 0;
    width: 45px; height: 80px;
    background: var(--grey);
  }
  .person-name { font-size: 27px; line-height: 1.1; }
  .person-role { font-size: 20px; line-height: 1.3; }

  .contact-list {
    position: absolute;
    left: 552px; top: 342px;
    list-style: none;
    font-size: 20px;
    line-height: 28px;
  }
  .contact-list b { font-style: italic; font-weight: 700; }

  .address {
    position: absolute;
    left: 43px; top: 398px;
    font-size: 20px;
    line-height: 28px;
    font-style: normal;
  }
</style>
</head>
<body>
  <section class="card card-front">
    <div class="brand"><span class="brand-mark"></span>KRL</div>
    <div class="name-band">
      <div class="person-name">Your Name</div>
      <div class="person-role">Designation</div>
    </div>
    <ul class="contact-list">
      <li><b>t</b> : 123-123-1234</li>
      <li><b>f</b> : 123-123-1234</li>
      <li><b>e</b> : info@krl-example.com.sa</li>
      <li><b>w</b> : www.krl-example.com.sa</li>
    </ul>
    <address class="address">1234, Suite# 123, Street Name<br>State Name, Country Code</address>
  </section>

  <section class="card card-back">
    <div class="brand"><span class="brand-mark"></span>KRL</div>
  </section>
</body>
</html>
```